Dental Implant Logo and Business Card for Local Dentist

Design a unique business card and a logo that incorporates a dental implant as a primary focal point or a part of the text. New logo design & business card needs to incorporate our businesses old star shaped logo (attached) and a dental implant, along with our business name. Star logo does not have to remain the exact same colors and can be any size. Looking for a warm, friendly (non-aggressive) design that uses colors in the blue-green palate, partial to mint-turquoise color similar to the images attached . SIMPLE IS GOOD, but looking for creativity to bring all the elements together. OK to incorporate a splash of color. I have attached a few images of implant logos I like along with our existing star shaped logo. *I have also uploaded some images that represent local landscapes & images for the back of the business card. I would like to include a silhouette or sketch that represents one one of these areas on the back of the business card to convey the connection to our community and local roots of our business since we are 4th generation members of this community . Can visit our dental practice website for more info. www.hartwellandodegarddentalcare.example Card Must Haves on Front of Card:1. business name "Hartwell & Odegard Dental Care" 2. My Name: "Colin Odegard D.D.S."3. Phone # (925) 754-6020Other info for card (can be front or back)Address: 7840 Quarry Ridge Rd. #2C Larkmont, Wa 94531e-mail: millerandsimarrodentalcare@gmail.comcosmetic, family, & impDesign a unique business card and a logo that incorporates a dental implant as a primary focal point or a part of the text. New logo design & business card needs to incorporate our businesses old star shaped logo (attached) and a dental implant, along with our business name. Star logo does not have to remain the exact same colors and can be any size. Looking for a warm, friendly (non-aggressive) design that uses colors in the blue-green palate, partial to mint-turquoise color similar to the images attached . SIMPLE IS GOOD, but looking for creativity to bring all the elements together. OK to incorporate a splash of color. I have attached a few images of implant logos I like along with our existing star shaped logo. *I have also uploaded some images that represent local landscapes & images for the back of the business card. I would like to include a silhouette or sketch that represents one one of these areas on the back of the business card to convey the connection to our community and local roots of our business since we are 4th generation members of this community . Can visit our dental practice website for more info. www.hartwellandodegarddentalcare.example Card Must Haves on Front of Card:1. business name "Hartwell & Odegard Dental Care" 2. My Name: "Colin Odegard D.D.S."3. Phone # (925) 754-6020Other info for card (can be front or back)Address: 7840 Quarry Ridge Rd. #2C Larkmont, Wa 94531e-mail: millerandsimarrodentalcare@gmail.comcosmetic, family, & implant dentistry

Target Market(s)

Families

Industry/Entity Type

Dental

Contact Information for Business Card

See Project description above

Logo Text

Hartwell & Odegard Dental Care

Font styles to use
Serif

Colors
ffffff
33b8a4
87cfc6
0492cd
33a6d7
0255a3

Requirements
Must have
• *See Description...
• Card Must Haves on Front of Card:
• 1. business name "Hartwell & Odegard Dental Care"
• 2. My Name: "Colin Odegard D.D.S."
• 3. Phone # (555) 318-4297
• Other info for card (can be front or back)
• Address: 7840 Quarry Ridge Rd. #2C Larkmont, Wa 90217
• e-mail: hartwellandodegarddentalcare@example-mail.com
Nice to have
• Local image sketch or silhouette on back side of business card with remaining information on back: address, website, e-mail etc.

```html
<!DOCTYPE html>
<html lang="en">
<head>
<meta charset="utf-8">
<title>Hartwell &amp; Odegard Dental Care – Business Card</title>
<link href="https://fonts.googleapis.com/css2?family=Oswald:wght@600&family=Lato:wght@400;700&display=swap" rel="stylesheet">
<style>
  :root {
    --bg: #e4e4e4;
    --card: #ffffff;
    --teal: #33b8a4;
    --mint: #87cfc6;
    --blue: #0492cd;
    --sky: #33a6d7;
    --navy: #0255a3;
    --ink: #333a40;
    --rule: #9aa0a4;
  }
  * { box-sizing: border-box; margin: 0; padding: 0; }
  html, body { width: 1200px; height: 900px; overflow: hidden; }
  body { background: var(--bg); position: relative; font-family: "Lato", sans-serif; }

  .card {
    position: absolute;
    width: 520px;
    height: 298px;
    border-radius: 20px;
    overflow: hidden;
    box-shadow: 0 6px 18px rgba(0,0,0,0.18);
  }

  /* Back side: local landscape */
  .card-back { left: 80px; top: 120px; }
  .landscape {
    position: absolute; inset: 0;
    background: linear-gradient(180deg,
      #c9d9d6 0%, #b4cbc9 28%,
      #8c7a66 40%, #6f6456 55%,
      #4f73a0 62%, #3d5f8c 68%,
      #a8773f 76%, #8a5a2b 100%);
  }
  .back-logo {
    position: absolute; left: 0; right: 0; top: 112px;
    text-align: center; color: #ffffff;
    font-family: "Oswald", sans-serif; font-weight: 600;
    font-size: 24px; letter-spacing: 1px; text-transform: uppercase; line-height: 1.15;
  }

  /* Front side: contact details */
  .card-front { left: 600px; top: 470px; background: var(--card); padding: 32px 36px; }
  .brand-name {
    font-family: "Oswald", sans-serif; font-weight: 600;
    color: var(--teal); text-transform: uppercase;
    font-size: 28px; line-height: 1.1; letter-spacing: 0.5px;
  }
  .brand-rule { width: 300px; height: 1px; background: var(--rule); margin: 12px 0 18px; }
  .doctor {
    font-family: "Oswald", sans-serif; font-weight: 600;
    font-size: 21px; text-transform: uppercase; letter-spacing: 0.5px; margin-bottom: 8px;
  }
  .doctor .first { color: var(--teal); }
  .doctor .last { color: var(--blue); }
  .doctor .title { color: var(--sky); font-size: 16px; }
  .contact-list { list-style: none; font-size: 14px; color: var(--ink); }
  .contact-list li { display: flex; align-items: center; gap: 7px; line-height: 21px; }
  .contact-list svg { width: 12px; height: 12px; flex: none; }
</style>
</head>
<body>

<section class="card card-back" aria-label="Card back">
  <div class="landscape" role="img" aria-label="Photograph of a local mountain above a river with a long bridge and golden reeds in the foreground"></div>
  <p class="back-logo">Hartwell &amp; Odegard<br>Dental Care</p>
</section>

<section class="card card-front" aria-label="Card front">
  <p class="brand-name">Hartwell &amp; Odegard<br>Dental Care</p>
  <div class="brand-rule"></div>
  <p class="doctor"><span class="first">Colin</span> <span class="last">Odegard</span> <span class="title">D.D.S.</span></p>
  <ul class="contact-list">
    <li>
      <svg viewBox="0 0 12 12"><path fill="#0492cd" d="M2.5 1l2 2.2-1 1.3c.7 1.4 1.6 2.3 3 3l1.3-1 2.2 2-1.2 1.8C5 9.8 2.2 7 1 2.2z"/></svg>
      (555) 318-4297
    </li>
    <li>
      <svg viewBox="0 0 12 12"><rect x="0.5" y="2" width="11" height="8" rx="1" fill="#0492cd"/><path d="M1 2.6l5 4 5-4" stroke="#fff" stroke-width="1" fill="none"/></svg>
      hartwellandodegarddentalcare@example-mail.com
    </li>
    <li>
      <svg viewBox="0 0 12 12"><circle cx="6" cy="6" r="5.5" fill="#0492cd"/><path d="M.8 6h10.4M6 .5c-2.4 3-2.4 8 0 11M6 .5c2.4 3 2.4 8 0 11" stroke="#fff" stroke-width="0.8" fill="none"/></svg>
      www.hartwellandodegarddentalcare.example
    </li>
    <li>
      <svg viewBox="0 0 12 12"><path fill="#33b8a4" d="M6 .5a4 4 0 0 1 4 4c0 3-4 7-4 7s-4-4-4-7a4 4 0 0 1 4-4z"/><circle cx="6" cy="4.5" r="1.5" fill="#fff"/></svg>
      7840 Quarry Ridge Rd. #2C Larkmont, Wa 90217
    </li>
  </ul>
</section>

</body>
</html>
```